Robotic Physical Therapy office needs a Grand Opening Flyer

We need a Grand Opening flyer design for a robotic physical therapy office named Kinetic Harbor Wellness. We would like it to have a clean, classy, upscale feeling that gives potential clients a V.I.P. feeling. We would like to use the colors black, gray, and yellow (logo will be uploaded).

Event: Thursday, June 1st, 2023 from 12pm-6pm
location: 58274 Pellham Ave, Bloomfield Hills, MI 48519

Industry/Entity Type

Physical therapy

Font styles to use
Script

Colors

Designer to choose colors to be used in the design.

Requirements
Nice to have
• More of a vip feel for the invite

```html
<!DOCTYPE html>
<html lang="en">
<head>
<meta charset="utf-8">
<title>Kinetic Harbor Wellness — Grand Opening</title>
<link rel="stylesheet" href="https://fonts.googleapis.com/css2?family=Oswald:wght@600;700&family=Roboto:wght@700&family=Montserrat:wght@500;700&display=swap">
<style>
  :root {
    --ink: #141414;
    --night: #1b1b1b;
    --yellow: #ffd600;
    --yellow-light: #fff04a;
    --gold: #f5c400;
    --silver: #d8d9da;
    --text: #232323;
    --muted: #8a8a8a;
    --paper: #ffffff;
  }
  * { margin: 0; padding: 0; box-sizing: border-box; }
  html, body { width: 848px; height: 1200px; overflow: hidden; background: var(--paper); }
  .flyer { position: relative; width: 848px; height: 1200px; overflow: hidden; background: var(--paper); }

  .night-sky {
    position: absolute; left: 0; top: 0; width: 848px; height: 720px;
    background: radial-gradient(ellipse at 30% 30%, #2a2a2a 0%, var(--night) 45%, var(--ink) 100%);
  }

  .brand { position: absolute; left: 62px; top: 62px; display: flex; align-items: center; gap: 14px; }
  .brand-dot { width: 52px; height: 52px; border-radius: 50%; background: var(--yellow); flex: none; }
  .brand-name {
    font-family: "Montserrat", sans-serif; font-weight: 700; color: var(--paper);
    font-size: 30px; line-height: 1.1; letter-spacing: 0.5px;
  }

  .headline {
    position: absolute; left: 60px; top: 226px;
    font-family: "Oswald", sans-serif; font-weight: 700; text-transform: uppercase;
    background: linear-gradient(180deg, var(--yellow) 0%, var(--yellow-light) 55%, var(--gold) 100%);
    -webkit-background-clip: text; background-clip: text; color: transparent;
    line-height: 1;
  }
  .headline .line-grand { display: block; font-size: 156px; letter-spacing: 0; }
  .headline .line-opening { display: block; font-size: 122px; letter-spacing: 0; margin-top: 4px; }

  .ribbon-cut-art {
    position: absolute; left: 570px; top: 166px; width: 278px; height: 384px;
    background: linear-gradient(160deg, #d9b24a 0%, #ffd600 45%, #fff04a 62%, var(--silver) 85%, #bdbdbd 100%);
    border-radius: 24px 0 0 24px;
  }

  .wave-band { position: absolute; left: 0; top: 540px; width: 848px; height: 260px; }

  .service {
    position: absolute; left: 37px; top: 800px;
    font-family: "Roboto", sans-serif; font-weight: 700; color: var(--text);
    font-size: 58px; line-height: 1.12; letter-spacing: -0.5px;
  }

  .details { position: absolute; left: 30px; top: 980px; font-family: "Montserrat", sans-serif; color: var(--text); font-size: 23px; }
  .detail-row { display: flex; gap: 32px; }
  .detail-row + .detail-row { margin-top: 30px; }
  .detail-icon { width: 36px; flex: none; padding-top: 2px; }
  .detail-text { line-height: 1.5; font-weight: 500; }
  .detail-text strong { font-weight: 700; }
  .time-pill {
    display: inline-block; margin-left: 18px; padding: 0 18px; border-radius: 20px;
    background: var(--yellow); line-height: 32px;
  }

  .patient-photo {
    position: absolute; left: 510px; top: 700px; width: 338px; height: 494px;
    background: linear-gradient(180deg, #ececec 0%, #d3d3d3 55%, #f2f2f2 100%);
  }
</style>
</head>
<body>
<main class="flyer">
  <div class="night-sky" role="img" aria-label="Dark night background with soft golden sparkles"></div>

  <div class="ribbon-cut-art" role="img" aria-label="Gold scissors cutting a yellow and silver ribbon"></div>

  <svg class="wave-band" viewBox="0 540 848 260" aria-hidden="true">
    <defs>
      <linearGradient id="bandGrad" x1="0" y1="0" x2="1" y2="0">
        <stop offset="0" stop-color="#ffd600"/>
        <stop offset="0.55" stop-color="#ffec00"/>
        <stop offset="1" stop-color="#ffd000"/>
      </linearGradient>
    </defs>
    <path d="M0 570 C180 548 360 560 520 590 C660 615 760 612 848 600 L848 690 C620 690 420 692 200 720 C110 732 40 750 0 765 Z" fill="url(#bandGrad)"/>
    <path d="M0 625 C200 610 380 612 560 640 C700 660 780 660 848 655 L848 668 C700 675 520 680 340 700 C200 715 80 735 0 760 Z" fill="#ffe000" opacity="0.6"/>
    <path d="M0 765 C60 745 140 728 240 715 C420 695 640 688 848 690 L848 700 C630 700 420 712 260 730 C150 742 70 760 0 790 Z" fill="#ffd000"/>
  </svg>

  <header class="brand">
    <span class="brand-dot"></span>
    <span class="brand-name">KINETIC HARBOR<br>WELLNESS</span>
  </header>

  <h1 class="headline">
    <span class="line-grand">Grand</span>
    <span class="line-opening">Opening</span>
  </h1>

  <h2 class="service">Robotic<br>Physical Therapy</h2>

  <section class="details">
    <div class="detail-row">
      <svg class="detail-icon" viewBox="0 0 36 36" width="36" height="36" aria-hidden="true">
        <rect x="3" y="6" width="26" height="25" rx="3" fill="none" stroke="#8a8a8a" stroke-width="2"/>
        <line x1="3" y1="12" x2="29" y2="12" stroke="#8a8a8a" stroke-width="2"/>
        <line x1="10" y1="3" x2="10" y2="9" stroke="#8a8a8a" stroke-width="2"/>
        <line x1="22" y1="3" x2="22" y2="9" stroke="#8a8a8a" stroke-width="2"/>
        <circle cx="26" cy="28" r="6" fill="#fff" stroke="#8a8a8a" stroke-width="2"/>
        <path d="M26 25 V28 H28" fill="none" stroke="#8a8a8a" stroke-width="1.6"/>
      </svg>
      <p class="detail-text">Thursday, <strong>June 1st,</strong> 2023<br>from<span class="time-pill">12pm-6pm</span></p>
    </div>
    <div class="detail-row">
      <svg class="detail-icon" viewBox="0 0 36 36" width="36" height="36" aria-hidden="true">
        <path d="M18 3 C11 3 7 8 7 14 C7 21 18 31 18 31 C18 31 29 21 29 14 C29 8 25 3 18 3 Z" fill="#8a8a8a"/>
        <circle cx="18" cy="14" r="4.5" fill="#fff"/>
        <ellipse cx="18" cy="33" rx="10" ry="2" fill="none" stroke="#8a8a8a" stroke-width="1.5"/>
      </svg>
      <p class="detail-text">58274 Pellham Ave,<br>Bloomfield Hills, MI 48519</p>
    </div>
  </section>

  <div class="patient-photo" role="img" aria-label="Woman seated on a white robotic physical therapy machine"></div>
</main>
</body>
</html>
```